Classy, Elegant, Simple Business Card Design

Looking to have a classy, simple, and elegant design. Want a top notch designed business card. I really like the look of the new torvane credit card. I also like the design I attached. I am trying to reach 21-29 year old females for booking us for there wedding or event. We offer Disc Jockey Service, Photo Booth Rentals, and Uplighting .

Target Market(s)

21-28 year old females

Contact Information for Business Card

Has to have logo, website, email, and phone number

Font styles to use
Other font styles liked:
• open to font choice, modern, clean
Designer to choose
33a6d7
0791cd
0555a3
ffffff

Requirements
Must have
• Has to have logo, website, email, and phone number
Nice to have
• I really like the design of the new torvane credit card. I also included my logo and some designs I like
Should not have
• clutter or too much info

```html
<!DOCTYPE html>
<html lang="en">
<head>
<meta charset="utf-8">
<title>Tidewell Event Group – Business Card</title>
<link rel="stylesheet" href="https://fonts.googleapis.com/css2?family=Poppins:wght@400;500;600&display=swap">
<style>
  :root {
    --bg: #1f1f21;
    --white: #ffffff;
    --sky: #33a6d7;
    --azure: #0791cd;
    --royal: #0555a3;
    --navy: #1a4f88;
    --mist: #dfe3e8;
    --grey: #8a8f96;
  }
  html, body {
    margin: 0;
    width: 1200px;
    height: 1200px;
    overflow: hidden;
    background: var(--bg);
    font-family: "Poppins", sans-serif;
  }
  .stage { position: relative; width: 1200px; height: 1200px; }
  .card {
    position: absolute;
    left: 262px;
    width: 686px;
    height: 392px;
    box-shadow: 0 18px 30px rgba(0,0,0,0.55);
  }
  .card--front { top: 165px; background: var(--white); }
  .card--back { top: 653px; }
  .card svg { display: block; width: 100%; height: 100%; }
  .name { font-weight: 500; font-size: 27px; fill: var(--white); }
  .role { font-weight: 400; font-size: 18px; fill: var(--white); }
  .contact { font-weight: 400; font-size: 19px; fill: var(--white); }
  .brand { font-weight: 500; fill: var(--navy); }
  .brand-mark { font-weight: 500; fill: var(--mist); }
  .services { font-weight: 500; font-size: 19px; fill: var(--white); }
</style>
</head>
<body>
<div class="stage">

  <div class="card card--front">
    <svg viewBox="0 0 800 457" aria-label="Business card front">
      <defs>
        <linearGradient id="frontBlue" x1="0" y1="0" x2="1" y2="1">
          <stop offset="0" stop-color="var(--azure)"/>
          <stop offset="0.55" stop-color="#09a3e4"/>
          <stop offset="1" stop-color="#1183cf"/>
        </linearGradient>
      </defs>
      <path class="wave-fill" fill="url(#frontBlue)"
        d="M0,240 C120,205 280,225 420,298 C560,372 650,405 720,397 C760,390 785,345 800,312 L800,457 L0,457 Z"/>
      <path class="wave-sweep" fill="#1b8ed6"
        d="M0,188 C120,172 230,205 300,271 C210,216 90,205 0,218 Z"/>
      <path class="wave-line" fill="none" stroke="var(--navy)" stroke-width="9" stroke-linecap="round"
        d="M0,176 C150,158 310,200 440,272 C570,345 650,393 715,388 C758,384 785,342 800,306"/>

      <g class="logo" text-anchor="middle">
        <circle cx="607" cy="110" r="34" fill="var(--sky)"/>
        <text class="brand" x="607" y="210" font-size="36" letter-spacing="2">TIDEWELL</text>
        <text class="brand" x="607" y="232" font-size="15" letter-spacing="7">EVENT GROUP</text>
      </g>

      <text class="name" x="44" y="311">Daniel Brooks</text>
      <text class="role" x="44" y="334">President</text>

      <g class="icon-phone" fill="var(--white)" transform="translate(46,362)">
        <path d="M3,0 L6,0 L8,4 L6,6 C7,9 9,11 11,12 L13,10 L17,12 L17,15 C10,16 2,8 3,0 Z"/>
      </g>
      <text class="contact" x="70" y="376">555-014-2738</text>
      <g class="icon-mail" transform="translate(46,389)">
        <rect x="0" y="0" width="14" height="10" fill="var(--white)"/>
        <path d="M0,0 L7,6 L14,0" fill="none" stroke="#0b98dc" stroke-width="1.5"/>
      </g>
      <text class="contact" x="70" y="399">hello@tidewellevents.com</text>
      <g class="icon-globe" transform="translate(53,417)">
        <circle r="7.5" fill="var(--white)"/>
        <path d="M-4,-5 C-1,-3 -3,0 0,1 C2,2 1,5 3,6 M2,-6 C4,-4 6,-3 6,0" fill="none" stroke="#0b98dc" stroke-width="1.6"/>
      </g>
      <text class="contact" x="70" y="421">www.tidewellevents.com</text>
    </svg>
  </div>

  <div class="card card--back">
    <svg viewBox="0 0 800 457" aria-label="Business card back">
      <defs>
        <radialGradient id="backBlue" cx="0.5" cy="0.4" r="0.75">
          <stop offset="0" stop-color="#08a8e6"/>
          <stop offset="0.6" stop-color="#1696d8"/>
          <stop offset="1" stop-color="#1a7fc8"/>
        </radialGradient>
      </defs>
      <rect width="800" height="457" fill="url(#backBlue)"/>
      <g text-anchor="middle">
        <text class="brand-mark" x="400" y="248" font-size="92" letter-spacing="4">TIDEWELL</text>
        <text class="services" x="400" y="413">Disc Jockey Service • Photo Booth Rentals • Uplighting .</text>
      </g>
    </svg>
  </div>

</div>
</body>
</html>
```